Company Website for Varnoth Signal, an open source data analytics company focused on relationship and li

I need a company/brand website for our new startup, Varnoth Signal LLC. We are a company focused on using life pattern analysis techniques, looking at relationships and how relationships, attributes, and activity cluster to infer aggregate information about individuals and groups. Our focus is on improving the digital advertising market.

We have a company logo which I will upload shortly.

Target Market(s)

Digital Advertising

Number of Pages Required

3 page

Font styles to use
Sans Serif

Requirements
Must have
• An main page, about us, contact page.
Nice to have
• Varnoth Signal relies on state of the art analytics applied to a the digital marketing space. While it is heavy in science, we also understand the art of influence. The website should have a scientific edge but also a flair that illustrates our focus on applying the hard science and analytics to influencing the behavior of people.

```html
<!DOCTYPE html>
<html lang="en">
<head>
<meta charset="utf-8">
<title>Varnoth Signal</title>
<link rel="stylesheet" href="https://fonts.googleapis.com/css2?family=Open+Sans:wght@400;600;700&display=swap">
<style>
:root{
  --orange:#f28a1e;
  --orange-dark:#e8770c;
  --blue:#2a93d9;
  --brand-blue:#2d8fd6;
  --ink:#2b2b2b;
  --muted:#8a8f96;
  --text:#4a4a4a;
  --pale:#eef5fc;
  --review:#d3e7f6;
  --rule:#c7dcee;
  --dark:#222;
}
*{margin:0;padding:0;box-sizing:border-box}
html,body{width:1200px;height:3742px;overflow:hidden;background:#fff}
body{font-family:"Open Sans",sans-serif;color:var(--text);position:relative}
.abs{position:absolute}
.header{position:absolute;top:0;left:0;width:1200px;height:118px;background:#fff;z-index:3}
.brand{position:absolute;left:72px;top:30px;display:flex;align-items:center;gap:10px}
.brand-dot{width:22px;height:22px;border-radius:50%;background:var(--orange)}
.brand-name{font-size:28px;font-weight:700;color:var(--brand-blue);letter-spacing:.5px}
.call-tab{position:absolute;right:0;top:0;width:380px;height:50px;background:var(--orange);clip-path:polygon(22px 0,100% 0,100% 100%,0 100%);color:#fff;font-size:17px;display:flex;align-items:center;gap:10px;padding-left:62px}
.nav{position:absolute;top:74px;right:70px;display:flex;gap:39px;font-size:16px;font-weight:600;color:var(--ink)}
.hero{position:absolute;top:118px;left:0;width:1200px;height:620px}
.hero-box{position:absolute;left:220px;top:200px;width:760px;height:150px;background:rgba(35,35,40,.55)}
.hero-title{position:absolute;left:220px;top:228px;width:760px;text-align:center;color:#fff;font-size:34px;font-weight:700;line-height:42px}
.btn-orange{display:inline-flex;align-items:center;justify-content:center;background:var(--orange);color:#fff;font-size:13px;font-weight:700;border-radius:24px;letter-spacing:.5px}
.section-title{position:absolute;left:0;width:1200px;text-align:center;color:var(--orange);font-size:33px;font-weight:700}
.title-rule{position:absolute;left:530px;width:140px;height:3px;background:var(--rule)}
.lead{position:absolute;text-align:center;font-size:13.5px;line-height:24px;color:var(--text)}
.card{position:absolute;background:#fff;box-shadow:0 2px 8px rgba(0,0,0,.18)}
.solution-title{font-size:17px;font-weight:700;color:var(--orange);text-align:center;margin-top:26px}
.solution-text{font-size:14px;line-height:24px;color:#9aa0a6;text-align:center;padding:6px 26px 0}
.solution-btn{position:absolute;left:0;bottom:0;width:100%;height:42px;background:var(--blue);color:#fff;font-size:18px;display:flex;align-items:center;justify-content:center}
.avatar{width:74px;height:74px;border-radius:50%;background:linear-gradient(135deg,#c9a99a,#6d5a52);margin:60px auto 0}
.quote{font-size:13px;line-height:22px;text-align:center;color:var(--text);padding:22px 28px 0}
.person{text-align:center;font-size:17px;font-weight:600;color:var(--ink);margin-top:28px}
.role{text-align:center;font-size:11px;color:#666;margin-top:6px}
.news{position:absolute;left:160px;top:2475px;width:880px;height:56px;background:var(--dark);display:flex;align-items:center}
.news-label{width:112px;height:56px;background:var(--blue);color:#fff;font-size:24px;font-weight:700;display:flex;align-items:center;justify-content:center;position:relative}
.news-label::after{content:"";position:absolute;right:-14px;top:20px;border-left:14px solid var(--blue);border-top:8px solid transparent;border-bottom:8px solid transparent}
.news-text{color:#fff;font-size:16px;margin-left:40px;flex:1}
.news-arrows{display:flex;gap:22px;margin-right:26px}
.review{position:absolute;top:2660px;width:330px;height:257px;background:var(--review);text-align:center}
.stars{margin-top:36px;display:flex;justify-content:center;gap:10px}
.review-text{font-size:13px;line-height:22px;color:var(--text);padding:16px 34px 0}
.reviewer{font-size:15px;font-weight:700;color:var(--ink);margin-top:10px}
.faq-item{position:absolute;left:75px;width:1050px;background:#fff;border:1px solid #d6d6d6;border-radius:3px;height:64px;display:flex;align-items:center;justify-content:space-between;padding:0 22px 0 28px;font-size:21px;font-weight:600;color:var(--ink)}
.faq-answer{position:absolute;left:75px;top:3175px;width:1050px;height:72px;background:var(--review);font-size:16px;line-height:26px;color:var(--text);padding:10px 22px}
.footer-nav{position:absolute;top:3572px;left:0;width:1200px;display:flex;justify-content:center;gap:44px;font-size:16px;font-weight:600;color:var(--ink)}
.social{position:absolute;top:3623px;left:0;width:1200px;display:flex;justify-content:center;gap:32px}
.social span{width:16px;height:16px;border-radius:50%;background:var(--ink)}
.copyright{position:absolute;top:3668px;left:0;width:1200px;text-align:center;font-size:12px;color:#555}
</style>
</head>
<body>

<!-- Light section backgrounds -->
<svg class="abs" style="left:0;top:1100px" width="1200" height="800" aria-hidden="true">
  <path d="M0 90 Q600 -40 1200 90 L1200 800 L0 800 Z" fill="var(--pale)"/>
</svg>
<svg class="abs" style="left:0;top:1860px" width="1200" height="640" aria-hidden="true">
  <path d="M0 40 Q600 -40 1200 40 L1200 560 Q600 640 0 560 Z" fill="var(--pale)"/>
</svg>
<svg class="abs" style="left:0;top:2960px" width="1200" height="560" aria-hidden="true">
  <path d="M0 70 Q600 -40 1200 70 L1200 470 Q600 570 0 470 Z" fill="var(--pale)"/>
</svg>

<header class="header">
  <div class="brand"><span class="brand-dot"></span><span class="brand-name">Varnoth Signal</span></div>
  <div class="call-tab">
    <svg width="14" height="20" viewBox="0 0 14 20"><rect x="1" y="1" width="12" height="18" rx="2" fill="#fff"/><rect x="3" y="3" width="8" height="12" fill="var(--orange)"/></svg>
    Call Us : 1-800 555 0142
  </div>
  <nav class="nav"><span>Home</span><span>About Us</span><span>Services</span><span>Media</span><span>News</span><span>Contact Us</span></nav>
</header>

<section class="hero">
  <svg class="abs" style="left:0;top:0" width="1200" height="620">
    <defs>
      <linearGradient id="heroFill" x1="0" y1="0" x2="0" y2="1">
        <stop offset="0" stop-color="#6b7686"/>
        <stop offset=".55" stop-color="#3c4656"/>
        <stop offset="1" stop-color="#273243"/>
      </linearGradient>
      <clipPath id="heroClip"><path d="M0 12 Q600 -20 1200 12 L1200 540 Q600 660 0 540 Z"/></clipPath>
    </defs>
    <g clip-path="url(#heroClip)">
      <rect width="1200" height="620" fill="url(#heroFill)" role="img" aria-label="Business team seated in a row with analytics bar chart overlay"/>
      <g fill="#e8f3ff" opacity=".85">
        <rect x="20" y="300" width="18" height="320"/><rect x="60" y="360" width="18" height="260"/>
        <rect x="100" y="260" width="18" height="360"/><rect x="140" y="330" width="18" height="290"/>
        <rect x="180" y="230" width="18" height="390"/><rect x="220" y="390" width="18" height="230"/>
        <rect x="260" y="300" width="18" height="320"/><rect x="300" y="360" width="18" height="260"/>
        <rect x="880" y="330" width="18" height="290"/><rect x="920" y="250" width="18" height="370"/>
        <rect x="960" y="380" width="18" height="240"/><rect x="1000" y="320" width="18" height="300"/>
        <rect x="1040" y="220" width="18" height="400"/><rect x="1080" y="360" width="18" height="260"/>
        <rect x="1120" y="280" width="18" height="340"/><rect x="1160" y="340" width="18" height="280"/>
      </g>
      <line x1="0" y1="570" x2="1200" y2="570" stroke="#9fd0f2" stroke-width="1.5" opacity=".6"/>
      <circle cx="445" cy="570" r="12" fill="#bfe6ff"/><circle cx="760" cy="570" r="12" fill="#bfe6ff"/>
    </g>
    <g fill="#fff">
      <rect x="548" y="540" width="12" height="12" transform="rotate(45 554 546)"/>
      <rect x="580" y="540" width="12" height="12" transform="rotate(45 586 546)" opacity=".7"/>
      <rect x="612" y="540" width="12" height="12" transform="rotate(45 618 546)"/>
      <rect x="644" y="540" width="12" height="12" transform="rotate(45 650 546)" opacity=".7"/>
    </g>
  </svg>
  <div class="hero-box"></div>
  <h1 class="hero-title">We are a company focused on using life<br>pattern analysis techniques</h1>
  <a class="btn-orange abs" style="left:513px;top:335px;width:174px;height:44px">ANALYSIS</a>
</section>

<h2 class="section-title" style="top:785px">Why Varnoth Signal</h2>
<p class="lead" style="left:190px;top:858px;width:820px">Nor again is there anyone who loves or pursues or desires to obtain pain of itself, because it is pain, but because occasionally circumstances occur in which toil and pain can procure him some great pleasure. To take a trivial example, which of us ever undertakes laborious physical exercise, except to obtain some advantage from it? But who has any right to find fault with a man who chooses to enjoy a pleasure that has no annoying consequences, or one who avoids a pain that produces no resultant pleasure</p>
<a class="btn-orange abs" style="left:513px;top:1005px;width:174px;height:44px">READ MORE</a>

<h2 class="section-title" style="top:1195px">Our Solutions</h2>
<div class="title-rule" style="top:1265px"></div>
<p class="lead" style="left:130px;top:1285px;width:940px">Sed ut perspiciatis unde omnis iste natus error sit voluptatem accusantium doloremque laudantium, totam rem aperiam, eaque ipsa quae ab illo inventore veritatis et quasi architecto beatae vitae dicta sunt explicabo.</p>

<div class="card" style="left:60px;top:1380px;width:345px;height:410px">
  <svg width="345" height="228" role="img" aria-label="Parent and child playing together at home"><path d="M0 0H345V210Q172 236 0 210Z" fill="#a08a7c"/></svg>
  <div class="solution-title">LIFE</div>
  <div class="solution-text">Nor again is there anyone who loves or pursues or desires to obtain pain of itself, because it is pain,</div>
  <div class="solution-btn">Read More</div>
</div>
<div class="card" style="left:427px;top:1380px;width:345px;height:410px">
  <svg width="345" height="228" role="img" aria-label="Couple sitting close together by a bright window"><path d="M0 0H345V210Q172 236 0 210Z" fill="#b9aea6"/></svg>
  <div class="solution-title">RELATIONSHIPS</div>
  <div class="solution-text">Nor again is there anyone who loves or pursues or desires to obtain pain of itself, because it is pain,</div>
  <div class="solution-btn">Read More</div>
</div>
<div class="card" style="left:795px;top:1380px;width:345px;height:410px">
  <svg width="345" height="228" role="img" aria-label="Older woman stretching outdoors in a sunny park"><path d="M0 0H345V210Q172 236 0 210Z" fill="#8d9a6a"/></svg>
  <div class="solution-title">ACTIVITY</div>
  <div class="solution-text">Nor again is there anyone who loves or pursues or desires to obtain pain of itself, because it is pain,</div>
  <div class="solution-btn">Read More</div>
</div>

<h2 class="section-title" style="top:1962px">Testimonials</h2>
<div class="title-rule" style="top:2040px"></div>

<div class="card" style="left:75px;top:2075px;width:330px;height:365px">
  <div class="avatar" role="img" aria-label="Client portrait"></div>
  <p class="quote">"Suspendisse et quis. Ante est feugiat. Urna odio tristique. Amet vel semper. Turpis hac in mattis quam placerat tincidunt magna aliquet"</p>
  <div class="person">Alira</div><div class="role">Freelancer, Belgium</div>
</div>
<div class="card" style="left:435px;top:2075px;width:330px;height:365px">
  <div class="avatar" role="img" aria-label="Client portrait" style="background:linear-gradient(135deg,#e3cbb8,#a88a74)"></div>
  <p class="quote">"Suspendisse et quis. Ante est feugiat. Urna odio tristique. Amet vel semper. Turpis hac in mattis quam placerat tincidunt magna aliquet"</p>
  <div class="person">Noveen</div><div class="role">Freelancer, Belgium</div>
</div>
<div class="card" style="left:795px;top:2075px;width:330px;height:365px">
  <div class="avatar" role="img" aria-label="Client portrait"></div>
  <p class="quote">"Suspendisse et quis. Ante est feugiat. Urna odio tristique. Amet vel semper. Turpis hac in mattis quam placerat tincidunt magna aliquet"</p>
  <div class="person">Kessa</div><div class="role">Freelancer, Belgium</div>
</div>

<div class="news">
  <div class="news-label">News</div>
  <div class="news-text">Lacus adipiscing scelerisque. Phasellus vulputate nulla. Morbi at dui hac amet</div>
  <div class="news-arrows">
    <svg width="10" height="16" viewBox="0 0 10 16"><path d="M8 2L2 8l6 6" stroke="#fff" stroke-width="2.5" fill="none"/></svg>
    <svg width="10" height="16" viewBox="0 0 10 16"><path d="M2 2l6 6-6 6" stroke="#fff" stroke-width="2.5" fill="none"/></svg>
  </div>
</div>

<h2 class="section-title" style="top:2567px">Reviews</h2>
<div class="title-rule" style="top:2627px"></div>

<div class="review" style="left:75px">
  <div class="stars"><svg width="140" height="18" viewBox="0 0 140 18"><g fill="var(--orange)"><path id="st" d="M9 0l2.6 6 6.4.5-4.9 4.1 1.6 6.4L9 13.6 3.3 17l1.6-6.4L0 6.5 6.4 6z"/><use href="#st" x="30"/><use href="#st" x="60"/><use href="#st" x="90"/><use href="#st" x="120"/></g></svg></div>
  <p class="review-text">Porta ultrices dolore ullamcorper volutpat est posuere pellentesque aut et eu vitae. Orci in turpis. Nulla cras aenean harum metus nulla.</p>
  <div class="reviewer">-Daren Holt</div>
</div>
<div class="review" style="left:435px">
  <div class="stars"><svg width="140" height="18" viewBox="0 0 140 18"><g fill="var(--orange)"><use href="#st"/><use href="#st" x="30"/><use href="#st" x="60"/><use href="#st" x="90"/><use href="#st" x="120"/></g></svg></div>
  <p class="review-text">Porta ultrices dolore ullamcorper volutpat est posuere pellentesque aut et eu vitae. Orci in turpis. Nulla cras aenean harum metus nulla.</p>
  <div class="reviewer">-Tamsel</div>
</div>
<div class="review" style="left:795px">
  <div class="stars"><svg width="140" height="18" viewBox="0 0 140 18"><g fill="var(--orange)"><use href="#st"/><use href="#st" x="30"/><use href="#st" x="60"/><use href="#st" x="90"/><use href="#st" x="120"/></g></svg></div>
  <p class="review-text">Porta ultrices dolore ullamcorper volutpat est posuere pellentesque aut et eu vitae. Orci in turpis. Nulla cras aenean harum metus nulla.</p>
  <div class="reviewer">-Orvin</div>
</div>

<h2 class="section-title" style="top:3017px">FAQ</h2>
<div class="title-rule" style="top:3077px"></div>

<div class="faq-item" style="top:3110px">Q . TEMPUS QUAM SAPIEN LEO HAC ELEMENTUM NULLA ?
  <svg width="18" height="12" viewBox="0 0 18 12"><path d="M2 10l7-7 7 7" stroke="var(--ink)" stroke-width="2.5" fill="none"/></svg></div>
<div class="faq-answer">Suspendisse et quis. Ante est feugiat. Urna odio tristique. Amet vel semper. Turpis hac in mattis quam placerat tincidunt magna aliquet.</div>
<div class="faq-item" style="top:3260px">Q . TEMPUS QUAM SAPIEN LEO HAC ELEMENTUM NULLA ?
  <svg width="12" height="18" viewBox="0 0 12 18"><path d="M2 2l7 7-7 7" stroke="var(--ink)" stroke-width="2.5" fill="none"/></svg></div>
<div class="faq-item" style="top:3335px">Q . TEMPUS QUAM SAPIEN LEO HAC ELEMENTUM NULLA ?
  <svg width="12" height="18" viewBox="0 0 12 18"><path d="M2 2l7 7-7 7" stroke="var(--ink)" stroke-width="2.5" fill="none"/></svg></div>

<footer>
  <nav class="footer-nav"><span>Home</span><span>About Us</span><span>Services</span><span>Media</span><span>News</span><span>Contact Us</span></nav>
  <div class="social" aria-label="Social links"><span></span><span></span><span></span><span></span></div>
  <p class="copyright">© 2018. Company Name &nbsp;|&nbsp; All Right Reserved</p>
</footer>

</body>
</html>
```